Lumavento business card

We need a modern business card - With our 4 colors - See web: www.lumavento.dk

I have attached logo and som old business Cards we have - Lets Make the new ones shine...:-) -

Industry/Entity Type

Business

Requirements
Must have
• the logo with lumavento only,

```html
<!DOCTYPE html>
<html lang="da">
<head>
<meta charset="utf-8">
<title>Lumavento – visitkort</title>
<link href="https://fonts.googleapis.com/css2?family=Source+Sans+3:wght@400;600&display=swap" rel="stylesheet">
<style>
  :root {
    --page-bg: #e4e4e2;
    --card-frost: #f3f5f2;
    --card-frost-edge: #dfe3dd;
    --green-dark: #3f8a25;
    --green-mid: #5fa83a;
    --green-light: #86c25a;
    --divider: #1c1c1c;
    --ink: #2b2b2b;
    --logo-ink: #3a3a3a;
    --rule: #6cb33f;
    --name-ink: #d2decb;
    --text-light: #eef5e8;
    --icon-light: #e4eedd;
  }
  html, body {
    margin: 0;
    padding: 0;
    width: 1200px;
    height: 969px;
    overflow: hidden;
    background: var(--page-bg);
    font-family: "Source Sans 3", Arial, sans-serif;
  }
  .canvas {
    position: relative;
    width: 1200px;
    height: 969px;
  }
  .business-card {
    position: absolute;
    left: 150px;
    top: 230px;
    width: 900px;
    height: 510px;
    border-radius: 30px;
    overflow: hidden;
    box-shadow: 0 10px 30px rgba(0,0,0,0.18);
  }
  .card-shapes {
    position: absolute;
    inset: 0;
  }
  .brand {
    position: absolute;
    left: 45px;
    top: 180px;
    width: 325px;
    text-align: center;
  }
  .brand-name {
    display: inline-flex;
    align-items: center;
    gap: 12px;
    font-size: 36px;
    font-weight: 400;
    letter-spacing: 1.5px;
    color: var(--logo-ink);
  }
  .brand-dot {
    width: 14px;
    height: 14px;
    border-radius: 50%;
    background: var(--green-mid);
  }
  .brand-rule {
    height: 3px;
    background: var(--rule);
    margin: 12px 0 14px;
  }
  .brand-tagline {
    font-size: 20px;
    color: var(--ink);
  }
  .contact {
    position: absolute;
    right: 42px;
    top: 48px;
    text-align: right;
    color: var(--text-light);
  }
  .person-name {
    margin: 0;
    font-size: 31px;
    font-weight: 600;
    color: var(--name-ink);
  }
  .person-title {
    margin: 2px 0 0;
    font-size: 23px;
    color: var(--text-light);
  }
  .address {
    margin: 108px 0 0;
    font-style: normal;
    font-size: 24px;
    line-height: 34px;
  }
  .contact-list {
    list-style: none;
    margin: 6px 0 0;
    padding: 0;
    font-size: 23px;
    line-height: 38px;
  }
  .contact-list li {
    display: flex;
    justify-content: flex-end;
    align-items: center;
    gap: 14px;
  }
  .contact-icon {
    width: 20px;
    height: 20px;
    flex: none;
  }
</style>
</head>
<body>
<main class="canvas">
  <section class="business-card" aria-label="Lumavento visitkort">
    <svg class="card-shapes" width="900" height="510" viewBox="0 0 900 510" aria-hidden="true">
      <defs>
        <linearGradient id="frost" x1="0" y1="0" x2="1" y2="1">
          <stop offset="0" stop-color="var(--card-frost)"/>
          <stop offset="1" stop-color="var(--card-frost-edge)"/>
        </linearGradient>
        <linearGradient id="green-field" x1="0" y1="0" x2="1" y2="0.6">
          <stop offset="0" stop-color="var(--green-dark)"/>
          <stop offset="0.55" stop-color="var(--green-mid)"/>
          <stop offset="1" stop-color="var(--green-light)"/>
        </linearGradient>
      </defs>
      <rect class="frost-field" width="900" height="510" fill="url(#frost)"/>
      <path class="divider-curve" d="M498,0 C552,110 500,390 180,510 L900,510 L900,0 Z" fill="var(--divider)"/>
      <path class="green-field" d="M512,0 C570,115 520,400 205,510 L900,510 L900,0 Z" fill="url(#green-field)"/>
    </svg>

    <div class="brand">
      <div class="brand-name"><span class="brand-dot"></span>lumavento</div>
      <div class="brand-rule"></div>
      <div class="brand-tagline">lys og idéer</div>
    </div>

    <div class="contact">
      <h1 class="person-name">Anders Mølgaard</h1>
      <p class="person-title">Salgsdirektør</p>
      <address class="address">Lindevej 14<br>5820 Vindeby Sø</address>
      <ul class="contact-list">
        <li>+45 31 42 67 80
          <svg class="contact-icon" viewBox="0 0 24 24" aria-hidden="true"><path fill="var(--icon-light)" d="M6.6 10.8a15.1 15.1 0 0 0 6.6 6.6l2.2-2.2a1 1 0 0 1 1-.25 11.4 11.4 0 0 0 3.6.57 1 1 0 0 1 1 1V20a1 1 0 0 1-1 1A17 17 0 0 1 3 4a1 1 0 0 1 1-1h3.5a1 1 0 0 1 1 1c0 1.250.2 2.45.57 3.57a1 1 0 0 1-.25 1z"/></svg>
        </li>
        <li>+45 52 19 73 46
          <svg class="contact-icon" viewBox="0 0 24 24" aria-hidden="true"><path fill="var(--icon-light)" d="M6.6 10.8a15.1 15.1 0 0 0 6.6 6.6l2.2-2.2a1 1 0 0 1 1-.25 11.4 11.4 0 0 0 3.6.57 1 1 0 0 1 1 1V20a1 1 0 0 1-1 1A17 17 0 0 1 3 4a1 1 0 0 1 1-1h3.5a1 1 0 0 1 1 1c0 1.250.2 2.45.57 3.57a1 1 0 0 1-.25 1z"/></svg>
        </li>
        <li>am@lumavento.dk
          <svg class="contact-icon" viewBox="0 0 24 24" aria-hidden="true"><rect x="2" y="5" width="20" height="14" rx="1.5" fill="var(--icon-light)"/><path d="M3 6.5l9 6.5 9-6.5" fill="none" stroke="var(--green-mid)" stroke-width="1.6"/></svg>
        </li>
        <li>www.lumavento.dk
          <svg class="contact-icon" viewBox="0 0 24 24" aria-hidden="true"><circle cx="12" cy="12" r="10" fill="var(--icon-light)"/><path d="M2 12h20M12 2c3 3 3 17 0 20M12 2c-3 3-3 17 0 20" fill="none" stroke="var(--green-mid)" stroke-width="1.4"/></svg>
        </li>
      </ul>
    </div>
  </section>
</main>
</body>
</html>
```